Business Card Design

We like to use greens as you will see in our logo (but not TOO much green). We are a Dental Clinic in a somewhat eccentric community. We do not like the dated sharp designs which we see many dentists use. We're looking for something bright and fresh while still maintaining the integrity of the profession. Elegance is not necessarily what we are going for... we need for the design to be "mature" but also up-lifting.

See our logo.
Updates

Project Deadline Extended
Reason: We have 5 designs which we like. But we'd like to see a few more before committing to a design.

Project Deadline Extended
Reason: We are awaiting revisions to this project. We are still welcoming designs while we wait to see if designers are able to provide to us the revisions we require in order to proceed with a selection.

Target Market(s)

Younger families - ages late 20's to early 40's

Industry/Entity Type

Business

Contact Information for Business Card

Corwel T. Banfry DDS 2730 W. Halvert Rd. Ste. 7 Larkmont, NE 48391 (248)555-0174 FX (248)555-0189 info@BrightwellDentalCareMi.com BrigthwellDentalCareMi.com on the back of the card we need an appointment reminder (For____ Date___ Time____) with "If you are unable to keep your appointment, kindly give 48 hours notice" at the bottom. No use of teeth in the design. DOUBLE SIDED DESIGN

Requirements
Should not have
• The use of pictures of teeth

```html
<!DOCTYPE html>
<html lang="en">
<head>
<meta charset="utf-8">
<title>Brightwell Dental Care – Business Card</title>
<link rel="stylesheet" href="https://fonts.googleapis.com/css2?family=Cinzel:wght@500&family=Source+Sans+3:ital,wght@0,400;0,600;0,700;1,400&display=swap">
<style>
  :root {
    --green-dark: #1f6a3a;
    --green-light: #8cc63f;
    --tree-faint: #b9d8a8;
    --ink: #2b2b2b;
    --card: #ffffff;
    --stage: #ecebe7;
    --rule: #9a9a9a;
    --field: #555555;
  }
  * { box-sizing: border-box; margin: 0; padding: 0; }
  html, body { width: 1200px; height: 1178px; overflow: hidden; }
  body {
    background: var(--stage);
    font-family: "Source Sans 3", "Helvetica Neue", Arial, sans-serif;
    color: var(--ink);
    position: relative;
  }
  .card {
    position: absolute;
    width: 915px;
    height: 520px;
    background: var(--card);
    box-shadow: 0 2px 6px rgba(0,0,0,.18);
    overflow: hidden;
  }
  .card--front { left: 249px; top: 46px; }
  .card--back  { left: 29px;  top: 626px; }

  /* Front */
  .brand {
    position: absolute; left: 0; right: 0; top: 110px;
    display: flex; align-items: center; justify-content: center; gap: 18px;
  }
  .brand__dot {
    width: 44px; height: 44px; border-radius: 50%;
    background: var(--green-light);
  }
  .brand__name {
    font-weight: 600; font-size: 62px; line-height: 1;
    color: var(--green-dark); letter-spacing: .5px;
  }
  .brand__rule {
    position: absolute; left: 278px; width: 360px; top: 196px;
    height: 3px; background: var(--green-light);
  }
  .brand__tagline {
    position: absolute; left: 0; right: 0; top: 204px; text-align: center;
    font-size: 40px; color: var(--green-dark); letter-spacing: 1px;
  }
  .band-rule { position: absolute; left: 0; right: 0; height: 3px; background: var(--green-light); }
  .band-rule--top { top: 275px; }
  .band-rule--bottom { top: 348px; }
  .name-band {
    position: absolute; left: 0; right: 0; top: 287px; height: 54px;
    background: var(--green-dark); color: #fff;
    display: flex; align-items: center; justify-content: center;
  }
  .name-band__name { font-weight: 700; font-size: 31px; }
  .name-band__title { font-size: 23px; margin-left: 8px; }

  .contact { position: absolute; top: 378px; font-size: 22px; line-height: 40px; }
  .contact--left { right: 495px; text-align: right; }
  .contact--right { left: 454px; }
  .contact__row { display: flex; align-items: center; gap: 6px; white-space: nowrap; }
  .contact--left .contact__row { justify-content: flex-end; }
  .contact__address { line-height: 33px; margin-top: 7px; white-space: nowrap; }
  .contact__divider {
    position: absolute; left: 438px; top: 383px; width: 2px; height: 106px;
    background: var(--rule);
  }
  .icon { width: 18px; height: 18px; fill: var(--green-dark); flex: none; }

  /* Back */
  .back-mark {
    position: absolute; left: 305px; top: 34px; width: 310px; height: 310px;
    border-radius: 50%; background: var(--tree-faint); opacity: .55;
  }
  .appt__title {
    position: absolute; left: 0; right: 0; top: 86px; text-align: center;
    font-family: "Cinzel", Georgia, serif; font-weight: 500;
    font-size: 35px; color: var(--green-dark); letter-spacing: 1px;
  }
  .appt__label { position: absolute; font-size: 26px; }
  .appt__dots {
    position: absolute; height: 0; border-bottom: 3px dotted var(--field);
  }
  .appt__box {
    position: absolute; width: 165px; height: 36px;
    border: 2px solid var(--field); border-radius: 5px;
  }
  .days {
    position: absolute; left: 70px; top: 369px;
    display: flex; align-items: center; gap: 14px;
  }
  .days__item { display: flex; align-items: center; gap: 12px; font-weight: 600; font-size: 26px; }
  .days__box { width: 55px; height: 36px; border: 2px solid var(--field); border-radius: 5px; }
  .days__item + .days__item { margin-left: 4px; }
  .appt__notice {
    position: absolute; left: 0; right: 0; top: 450px; text-align: center;
    font-style: italic; font-size: 27px; white-space: nowrap;
  }
</style>
</head>
<body>

<section class="card card--front" aria-label="Front of card">
  <div class="brand">
    <span class="brand__dot"></span>
    <span class="brand__name">Brightwell</span>
  </div>
  <div class="brand__rule"></div>
  <div class="brand__tagline">DENTAL CARE</div>

  <div class="band-rule band-rule--top"></div>
  <div class="name-band">
    <span class="name-band__name">Corwel T. Banfry,</span>
    <span class="name-band__title">DDS</span>
  </div>
  <div class="band-rule band-rule--bottom"></div>

  <div class="contact contact--left">
    <div class="contact__row">
      <svg class="icon" viewBox="0 0 24 24"><path d="M6.6 10.8a15 15 0 0 0 6.6 6.6l2.2-2.2c.3-.3.7-.4 1-.2 1.1.4 2.3.6 3.6.6.6 0 1 .4 1 1V20c0 .6-.4 1-1 1A17 17 0 0 1 3 4c0-.6.4-1 1-1h3.5c.6 0 1 .4 1 1 0 1.3.2 2.5.6 3.6.1.3 0 .7-.2 1z"/></svg>
      <span>(555)555-0174</span>
    </div>
    <div class="contact__address">2730 W. Halvert Rd.<br>Ste. 7 Larkmont NE 48391</div>
  </div>
  <div class="contact__divider"></div>
  <div class="contact contact--right">
    <div class="contact__row">
      <svg class="icon" viewBox="0 0 24 24"><path d="M6 4h9v5h3l3 3v7h-2a2 2 0 0 1-4 0H9a2 2 0 0 1-4 0H3V9l3-1zm2 2v3h5V6z"/></svg>
      <span>(555)555-0189</span>
    </div>
    <div class="contact__row">
      <svg class="icon" viewBox="0 0 24 24"><path d="M3 5h18v14H3zm2 2v.5l7 5 7-5V7z"/></svg>
      <span>info@BrightwellDentalCareMi.com</span>
    </div>
    <div class="contact__row">
      <svg class="icon" viewBox="0 0 24 24"><path d="M12 2a10 10 0 1 0 0 20 10 10 0 0 0 0-20zm6.9 9h-3a15 15 0 0 0-1.3-5.9A8 8 0 0 1 18.9 11zM12 4c.9 1.3 1.8 3.9 1.9 7h-3.8c.1-3.1 1-5.7 1.9-7zM9.4 5.1A15 15 0 0 0 8.1 11h-3a8 8 0 0 1 4.3-5.9zM5.1 13h3a15 15 0 0 0 1.3 5.9A8 8 0 0 1 5.1 13zM12 20c-.9-1.3-1.8-3.9-1.9-7h3.8c-.1 3.1-1 5.7-1.9 7zm2.6-1.1a15 15 0 0 0 1.3-5.9h3a8 8 0 0 1-4.3 5.9z"/></svg>
      <span>BrigthwellDentalCareMi.com</span>
    </div>
  </div>
</section>

<section class="card card--back" aria-label="Back of card">
  <div class="back-mark"></div>
  <h2 class="appt__title">YOUR APPOINTMENT</h2>

  <span class="appt__label" style="left:72px;top:153px;">Name :</span>
  <span class="appt__dots" style="left:172px;width:698px;top:180px;"></span>

  <span class="appt__label" style="left:72px;top:218px;">Date :</span>
  <span class="appt__dots" style="left:172px;width:228px;top:245px;"></span>
  <span class="appt__label" style="left:408px;top:218px;">Time :</span>
  <span class="appt__dots" style="left:493px;width:242px;top:245px;"></span>
  <span class="appt__label" style="left:741px;top:218px;">am / pm</span>

  <span class="appt__label" style="left:72px;top:283px;">Next Appointment</span>
  <span class="appt__box" style="left:326px;top:283px;"></span>
  <span class="appt__box" style="left:504px;top:283px;"></span>
  <span class="appt__box" style="left:679px;top:283px;"></span>

  <div class="days">
    <span class="days__item">MON <span class="days__box"></span></span>
    <span class="days__item">TUE <span class="days__box"></span></span>
    <span class="days__item">WED <span class="days__box"></span></span>
    <span class="days__item">THU <span class="days__box"></span></span>
    <span class="days__item">FRI <span class="days__box"></span></span>
    <span class="days__item">SAT <span class="days__box"></span></span>
  </div>

  <p class="appt__notice">If you are unable to keep your appointment, kindly give 48 hours notice</p>
</section>

</body>
</html>
```